Creation of an elegant and modern turnkey Shopify website

Hello,

We are a new company specializing in the sale of above-ground pools. We want to create a turnkey website, ideally using Shopify. For now, we need a "showcase" site, not an e-commerce platform, with four tabs:

Home Page (an overall presentation of the company)
Our Products (an overview of all the above-ground pools we sell)
Our Projects (a page inspired by Instagram to showcase photos of our future projects)
Contact (a page with all our contact information and a contact form)

We are looking to create a highly visual, elegant, and modern website with vibrant splashes of color. We will provide the text, photos (along with instructions on where to place them on each page), and all other necessary information as attachments.

Thank you in advance for your proposals!

The Brisa Lagoon Team

Target Market(s)

Targeted at Swiss customers (a translator will need to be installed for different languages)

Industry/Entity Type

Sale of customised above-ground pools

Coding

Coded - Design and coding required

Font styles to use
Sans Serif

Colors
0094D4
00A9DD
6FCCEA
C7EBF8
E9F6FB
00AB8E
00BBA5
67D7C9
C6EFE9
E9F9F6

Requirements
Must have
• A stunning, elegant and modern look
Nice to have
• Inspiration from the colors of our logo throughout the site, but in an elegant way
Should not have
• An overly classic look for swimming pool sites

```html
<!DOCTYPE html>
<html lang="en">
<head>
<meta charset="utf-8">
<title>Brisa Lagoon – Premium Above-Ground Pools</title>
<link href="https://fonts.googleapis.com/css2?family=Poppins:wght@300;400;500&display=swap" rel="stylesheet">
<style>
:root{
  --blue-dark:#0094D4;
  --blue:#00A9DD;
  --blue-mid:#6FCCEA;
  --blue-light:#C7EBF8;
  --blue-pale:#E9F6FB;
  --green-dark:#00AB8E;
  --green:#00BBA5;
  --green-mid:#67D7C9;
  --green-light:#C6EFE9;
  --green-pale:#E9F9F6;
  --ink:#111;
  --text:#555;
  --white:#fff;
}
*{box-sizing:border-box;margin:0;padding:0}
html,body{width:1200px;height:2461px;overflow:hidden}
body{font-family:'Poppins',sans-serif;color:var(--ink);background:var(--white);position:relative}
a{color:inherit;text-decoration:none}
.site-header{position:absolute;top:0;left:0;width:1200px;height:83px;background:var(--white);box-shadow:0 2px 8px rgba(0,0,0,.06);z-index:2}
.brand{position:absolute;left:74px;top:30px;font-size:15px;font-weight:300;color:var(--blue-mid);letter-spacing:.5px}
.nav{position:absolute;left:478px;top:23px;display:flex;align-items:center}
.nav a{font-size:12px;padding:0 17px;line-height:36px}
.nav a.active{background:var(--blue);color:var(--white);width:85px;text-align:center;border-radius:2px;padding:0;margin-right:16px}
.search{position:absolute;left:908px;top:23px;width:225px;height:36px;border:1px solid #bbb;border-radius:3px;display:flex;align-items:center;padding-left:12px;font-size:11px;color:#999;gap:12px}
.row{position:absolute;left:0;width:1200px}
.panel{position:absolute;top:0;height:100%}
.photo{position:absolute;top:0;height:100%}
.copy{position:absolute}
.copy h1,.copy h2{font-weight:500;color:var(--ink);white-space:nowrap}
.copy p{font-size:12px;line-height:20px;color:var(--text);text-align:justify;font-weight:300}
.btn{display:inline-block;color:var(--white);font-size:15px;font-weight:300;line-height:51px;padding:0 25px;border-radius:2px;margin-top:28px}
.btn-blue{background:var(--blue)}
.btn-green{background:var(--green)}
.hero{top:83px;height:457px}
.hero h1{font-size:29px;line-height:45px;margin-bottom:18px}
.why{top:547px;height:423px;background:linear-gradient(135deg,#cdeff5,#e4f7f9 40%,#c4ecf2 70%,#def5f7)}
.why h2{position:absolute;top:52px;width:100%;text-align:center;font-size:30px;line-height:42px;font-weight:500}
.features{position:absolute;top:164px;left:50px;display:flex}
.feature{width:220px;text-align:center}
.feature .icon{width:58px;height:58px;background:var(--green-dark);margin:0 auto 18px;display:flex;align-items:center;justify-content:center}
.feature h3{font-size:17px;font-weight:500;line-height:25px;margin-bottom:4px}
.feature p{font-size:12px;line-height:20px;color:var(--text);font-weight:300;padding:0 8px}
.section-title{font-size:30px;line-height:45px;margin-bottom:16px}
.footer{position:absolute;top:2152px;left:0;width:1200px;height:309px;background:var(--blue);color:var(--white)}
.footer h4{font-size:15px;font-weight:500;margin-bottom:12px}
.footer .col{position:absolute;font-size:11.5px;line-height:22px;font-weight:300}
.footer-brand{font-size:15px;font-weight:300;color:var(--blue-mid)}
.newsletter input{display:block;width:309px;height:41px;border:none;border-radius:2px;padding-left:15px;font-family:inherit;font-size:11px;color:#999;margin-bottom:10px}
.subscribe{display:inline-block;background:var(--white);color:var(--blue);font-size:12px;width:105px;line-height:37px;text-align:center;border-radius:2px}
.social{display:flex;gap:6px;margin-top:6px}
.social span{width:26px;height:26px;border-radius:50%;background:var(--white)}
.footer-rule{position:absolute;left:67px;top:256px;width:1066px;height:1px;background:rgba(255,255,255,.6)}
.copyright{position:absolute;top:274px;width:100%;text-align:center;font-size:11.5px;font-weight:300}
</style>
</head>
<body>
<header class="site-header">
  <div class="brand">Brisa Lagoon</div>
  <nav class="nav">
    <a class="active" href="#">Home</a>
    <a href="#">Our Products</a>
    <a href="#">Our Projects</a>
    <a href="#">Contact Us</a>
  </nav>
  <div class="search">
    <svg width="12" height="12" viewBox="0 0 12 12"><circle cx="5" cy="5" r="3.8" fill="none" stroke="#999" stroke-width="1.4"/><line x1="8" y1="8" x2="11" y2="11" stroke="#999" stroke-width="1.4"/></svg>
    Search
  </div>
</header>

<section class="row hero">
  <div class="panel" style="left:0;width:492px;background:var(--blue-pale)"></div>
  <div class="photo" style="left:500px;width:700px;background:linear-gradient(180deg,#3f7a3a 0%,#6aa352 38%,#7ed3e6 52%,#4fc4e0 80%,#7fd8ea 100%)" role="img" aria-label="Luxury pool with stepping stones and a pergola among palm trees"></div>
  <div class="copy" style="left:67px;top:58px;width:358px">
    <h1>Transform Your Garden<br>with Our Premium<br>Above-Ground Pools!</h1>
    <p>Imagine an exceptional relaxation and leisure space right in your own backyard. With our unparalleled expertise and commitment to excellence, we create above-ground pools that exceed all expectations. Our exclusive, custom-designed models are crafted to combine style, durability, and innovation, offering a unique and refined experience.</p>
    <a class="btn btn-blue" href="#">Explore Now →</a>
  </div>
</section>

<section class="row why">
  <h2>Why Choose<br>Our Above-Ground Pools?</h2>
  <div class="features">
    <div class="feature">
      <div class="icon"><svg width="32" height="32" viewBox="0 0 32 32" fill="none" stroke="#fff" stroke-width="1.3"><circle cx="16" cy="19" r="8"/><path d="M16 14l1.5 3 3.3.4-2.4 2.2.6 3.3-3-1.6-3 1.6.6-3.3-2.4-2.2 3.3-.4z"/><path d="M10 4l6 8 6-8"/></svg></div>
      <h3>Superior Quality</h3>
      <p>Each pool is constructed with high-quality materials, ensuring exceptional durability and strength.</p>
    </div>
    <div class="feature">
      <div class="icon"><svg width="32" height="32" viewBox="0 0 32 32" fill="none" stroke="#fff" stroke-width="1.3"><rect x="5" y="5" width="22" height="22"/><path d="M9 10h8M9 14h5M9 18h8M20 9v14M9 23h14"/></svg></div>
      <h3>Elegant Design</h3>
      <p>Our pools come in a variety of styles and finishes, seamlessly blending into any garden setting.</p>
    </div>
    <div class="feature">
      <div class="icon"><svg width="32" height="32" viewBox="0 0 32 32" fill="none" stroke="#fff" stroke-width="1.3"><circle cx="16" cy="16" r="4"/><circle cx="16" cy="16" r="8" stroke-dasharray="3 2"/><circle cx="16" cy="16" r="11"/></svg></div>
      <h3>Custom<br>and Tailor-Made</h3>
      <p>Create the pool of your dreams with our customization options, tailored to your specific tastes and needs.</p>
    </div>
    <div class="feature">
      <div class="icon"><svg width="32" height="32" viewBox="0 0 32 32" fill="none" stroke="#fff" stroke-width="1.3"><path d="M5 24h22M7 20l6-10 5 6 3-3 5 7"/><path d="M22 6l4 4M26 6l-4 4"/></svg></div>
      <h3>Easy Installation</h3>
      <p>Enjoy your new oasis quickly with our simple and fast installation process.</p>
    </div>
    <div class="feature">
      <div class="icon"><svg width="32" height="32" viewBox="0 0 32 32" fill="none" stroke="#fff" stroke-width="1.3"><path d="M11 18a7 7 0 1 1 10 0c-1 1-1.5 2-1.5 3.5h-7C12.5 20 12 19 11 18z"/><path d="M13 25h6M14 28h4"/></svg></div>
      <h3>Constant Innovation</h3>
      <p>We incorporate the latest technologies to provide you with an optimal and safe swimming experience.</p>
    </div>
  </div>
</section>

<section class="row" style="top:978px;height:383px">
  <div class="photo" style="left:0;width:700px;background:linear-gradient(135deg,#2fb0d2 0%,#6b6a66 40%,#8fbf4e 75%,#4f8f30 100%)" role="img" aria-label="Poolside deck with sun loungers and white parasols"></div>
  <div class="panel" style="left:708px;width:492px;background:var(--blue-pale)"></div>
  <div class="copy" style="left:775px;top:82px;width:358px">
    <h2 class="section-title">Personalized Services</h2>
    <p>We understand that every garden and client is unique. That's why we offer personalized services, from design to installation and after-sales support. Our team of experts is here to answer all your questions and guide you throughout your project.</p>
    <a class="btn btn-blue" href="#">Learn More →</a>
  </div>
</section>

<section class="row" style="top:1370px;height:383px">
  <div class="panel" style="left:0;width:492px;background:var(--green-pale)"></div>
  <div class="photo" style="left:500px;width:700px;background:linear-gradient(120deg,#5a3a33 0%,#8e9aa0 30%,#2fc0e6 55%,#5fd3ef 100%)" role="img" aria-label="Stainless steel pool ladder over clear blue water"></div>
  <div class="copy" style="left:67px;top:54px;width:358px">
    <h2 class="section-title">Guaranteed<br>Satisfaction</h2>
    <p>Your satisfaction is our top priority. We are committed to providing you with exceptional service and the highest quality products. Join our community of satisfied customers who are already enjoying their custom above-ground pools. 10-Year Warranty!</p>
    <a class="btn btn-green" href="#">Join Our Community →</a>
  </div>
</section>

<section class="row" style="top:1761px;height:383px">
  <div class="photo" style="left:0;width:700px;background:linear-gradient(170deg,#4f8a2e 0%,#8cbf4a 25%,#3aaed6 50%,#62c3e4 75%,#d9dcdc 100%)" role="img" aria-label="Pool edge with handrail in front of lush tropical plants"></div>
  <div class="panel" style="left:708px;width:492px;background:var(--blue-pale)"></div>
  <div class="copy" style="left:775px;top:92px;width:358px">
    <h2 class="section-title">Contact Us Today</h2>
    <p>Don't wait any longer to transform your garden into a wellness oasis. Contact us today to discover our range of customizable above-ground pools and get a tailored quote. Dive into a world of infinite possibilities with Brisa Lagoon.</p>
    <a class="btn btn-blue" href="#">Contact Us →</a>
  </div>
</section>

<footer class="footer">
  <div class="col" style="left:67px;top:50px;width:268px">
    <div class="footer-brand">Brisa Lagoon</div>
    <p style="margin-top:30px;text-align:justify;line-height:20px">At Brisa Lagoon, we create custom, premium above-ground pools that turn your garden into a luxurious oasis. Our high-quality materials and innovative designs ensure durability and seamless integration into any garden setting.</p>
  </div>
  <div class="col" style="left:415px;top:40px">
    <h4>Quick Links</h4>
    <div>Home</div><div>Our Products</div><div>Our Projects</div><div>Contact Us</div><div>Support</div><div>Privacy Policy</div><div>Terms &amp; Condition</div>
  </div>
  <div class="col" style="left:598px;top:40px">
    <h4>Contact</h4>
    <div>Marco Vellini</div><div>Chemin des Lilas 28</div><div>1860 Aigle</div><div>079 555 01 23</div>
    <h4 style="margin-top:18px;margin-bottom:4px">Stay Connected</h4>
    <div class="social"><span></span><span></span><span></span></div>
  </div>
  <div class="col newsletter" style="left:824px;top:34px">
    <h4>Newsletter</h4>
    <input type="text" placeholder="Write your email">
    <span class="subscribe">Subscribe</span>
  </div>
  <div class="footer-rule"></div>
  <div class="copyright">© 2024 Brisa Lagoon. All rights reserved.</div>
</footer>
</body>
</html>
```